life insurance quote website design for lepontdoriole.ca

the web site lepontdoriole.ca need a design. we dont like the actuel one but we are open at all new suggestion. visit us at lepontdoriole.ca and you will understand. the principal concurant is tarifsgarantisnord.ca, calculeo.ca, coutprotecfam.ca. We are a life insurance quote site. we found best price available in the canadien industrie. We absolutly want a design with our form in the front page on the top right side like our concurance, we use wordpress at this time. we want to be able to switch language. and to have a logic form. we want to be able to change the color for each type of insurance quote page.we also need a blog in it to post news. and the site will be SEO accurate.

Target Market(s)

Get client fill the quote form

Industry/Entity Type

Insurance

Number of Pages Required

3 page

Font styles to use
Sans Serif

Requirements
Must have
• logic form on the top right first page
• page template for product info stuff, contact, and who we are, blog
• French site
• custum color
Nice to have
• Wordpress design will be appréciate
• switch language english/french

```html
<!DOCTYPE html>
<html lang="en">
<head>
<meta charset="utf-8">
<title>lepontdoriole.ca — Life Insurance Quotes</title>
<link rel="stylesheet" href="https://fonts.googleapis.com/css2?family=Raleway:wght@400;500;600;700&family=Oswald:wght@500&display=swap">
<style>
:root{
  --navy:#0b1d5a;
  --nav-top:#1d4fa3;
  --nav-bottom:#0f3277;
  --heading:#1a2a6c;
  --red:#d81d1d;
  --red-dark:#b01414;
  --text:#555a66;
  --muted:#8a8f99;
  --light:#f1f2f4;
  --footer:#3b3b3b;
  --footer-bottom:#2b2b2b;
  --footer-text:#d5d5d5;
  --white:#ffffff;
  --life:#2aa9df;
  --salary:#d9a04a;
  --mortgage:#5dbb55;
  --disease:#ee5f86;
}
*{box-sizing:border-box;margin:0;padding:0}
html,body{width:1200px;height:2400px;overflow:hidden;background:var(--white)}
body{font-family:'Raleway',Arial,sans-serif;color:var(--text);position:relative}
.abs{position:absolute}

/* top bar */
.topbar{top:0;left:0;width:1200px;height:86px;background:var(--white)}
.contact-line{left:75px;top:30px;font-size:17px;color:var(--heading);display:flex;align-items:center;gap:12px}
.contact-line svg{width:15px;height:15px;fill:var(--heading)}
.contact-line .sep{margin:0 6px}
.login-btn{left:940px;top:26px;width:105px;height:36px;background:var(--red);color:var(--white);font-size:13px;font-weight:700;display:flex;align-items:center;justify-content:center;gap:8px;border-radius:2px}
.lang{left:1065px;top:35px;font-size:13px;font-weight:600;color:var(--muted)}

.login-panel{left:812px;top:64px;width:233px;height:186px;background:var(--white);border:1px solid #ddd;box-shadow:0 2px 6px rgba(0,0,0,.15);z-index:5;padding:20px 15px}
.login-panel .field{height:35px;border:1px solid #ccc;border-radius:3px;font-size:12px;color:var(--muted);padding:9px 12px;margin-bottom:8px;background:#fafafa}
.login-panel .submit{height:34px;background:var(--navy);color:var(--white);font-size:13px;font-weight:600;display:flex;align-items:center;justify-content:center;border-radius:3px}
.login-panel .links{display:flex;justify-content:space-between;font-size:11px;margin-top:12px;color:var(--muted)}
.login-panel .links span:first-child{color:var(--red)}

/* nav */
.nav{top:86px;left:0;width:1200px;height:62px;background:linear-gradient(var(--nav-top),var(--nav-bottom))}
.nav ul{list-style:none;display:flex;height:62px;align-items:center;padding-left:75px}
.nav li{color:var(--white);font-size:13px;font-weight:600;margin-right:60px}
.nav li.has-sub::after{content:"⌄";margin-left:12px;font-size:12px}

/* hero */
.hero{top:148px;left:0;width:1200px;height:358px}
.hero-photo{left:0;top:0;width:866px;height:358px;background:linear-gradient(160deg,#b9cf8e 0%,#8fb35c 45%,#c8d9a8 70%,#7fa44a 100%)}
.hero-panel{left:866px;top:0;width:334px;height:358px;background:linear-gradient(90deg,rgba(40,80,25,.85),rgba(20,60,20,.95))}
.hero-panel p{font-family:'Oswald',Arial,sans-serif;font-weight:500;color:var(--white);text-transform:uppercase;font-size:32px;line-height:44px;left:14px;position:absolute}
.brand{left:110px;top:110px;display:flex;align-items:center;gap:14px;font-size:34px;font-weight:700;color:var(--white)}
.brand .dot{width:34px;height:34px;border-radius:50%;background:var(--red)}

/* categories */
.categories{top:506px;left:0;width:1200px;height:210px;background:linear-gradient(#ffffff,#e9eaec)}
.cat{position:absolute;top:52px;width:200px;margin-left:-100px;text-align:center}
.cat .circle{width:88px;height:88px;border-radius:50%;margin:0 auto;display:flex;align-items:center;justify-content:center;border:3px solid var(--white);box-shadow:0 0 0 1px #ddd}
.cat .circle svg{width:44px;height:44px;fill:var(--white)}
.cat h3{font-size:16px;font-weight:600;color:#333;margin-top:24px;letter-spacing:.5px}

/* intro */
.intro{left:75px;top:762px;width:690px}
.intro h1{font-size:29px;font-weight:600;color:var(--heading);margin-bottom:14px}
.intro p{font-size:13.5px;line-height:25.6px}
.checks{left:75px;top:1028px;width:690px;display:grid;grid-template-columns:395px 295px;row-gap:18px;font-size:14px;color:var(--heading);font-weight:500}
.checks span{display:flex;align-items:center;gap:10px}
.checks svg{width:14px;height:14px}
.rule{left:75px;top:1125px;width:690px;height:1px;background:#e2e2e2}

.feature{position:absolute;width:330px;display:flex;gap:20px}
.feature .icon{flex:0 0 64px;height:64px;border-radius:50%;background:#ececec;display:flex;align-items:center;justify-content:center}
.feature .icon svg{width:28px;height:28px;fill:var(--red)}
.feature h4{font-size:16px;font-weight:600;color:var(--heading);line-height:23px;margin-top:-2px}
.feature p{font-size:13.5px;line-height:23px;margin-top:4px;width:250px}
.feature .more{display:inline-block;margin-top:16px;background:#222;color:var(--white);font-size:13px;font-weight:600;padding:8px 22px;border-radius:3px}

/* quote form */
.quote{left:794px;top:716px;width:332px;height:811px;background:var(--navy);padding:0 18px}
.quote-tag{left:780px;top:762px;width:232px;height:46px;background:var(--red);color:var(--white);font-size:22px;font-weight:600;padding:9px 27px;clip-path:polygon(0 0,92% 0,100% 50%,92% 100%,0 100%)}
.quote h5{position:absolute;left:18px;font-size:17px;font-weight:600;color:var(--white);width:296px;border-bottom:1px solid #25397a;padding-bottom:10px}
.quote .row{position:absolute;left:18px;width:296px;display:flex;justify-content:space-between;align-items:center;font-size:13px;color:#d8dcea}
.quote .input{width:203px;height:36px;border-radius:3px;background:linear-gradient(#fff,#e9e9e9)}
.quote .select{width:152px;height:36px;border-radius:3px;background:linear-gradient(#fff,#e9e9e9);font-size:13px;color:var(--muted);padding:9px 12px;display:flex;justify-content:space-between}
.radio{width:13px;height:13px;border-radius:50%;background:var(--white);display:inline-block;vertical-align:middle;margin-right:10px}
.captcha{left:18px;top:1398px;width:144px;height:36px;background:#fafafa;border-radius:2px;font-size:16px;font-weight:700;letter-spacing:2px;color:#444;text-align:center;line-height:36px;font-style:italic}
.captcha-input{left:170px;top:1398px;width:144px;height:36px;border-radius:2px;background:linear-gradient(#fff,#e9e9e9)}
.get-quote{left:18px;top:1453px;width:296px;height:48px;background:linear-gradient(var(--red),var(--red-dark));color:var(--white);font-size:21px;font-weight:700;text-align:center;line-height:48px;border-radius:3px}

/* blog */
.blog{top:1568px;left:0;width:1200px;height:404px;background:var(--light)}
.blog h2{position:absolute;left:75px;top:30px;font-size:29px;font-weight:500;color:var(--heading)}
.blog .arrows{position:absolute;left:1088px;top:36px;font-size:26px;color:#999;letter-spacing:6px}
.post{position:absolute;top:83px;width:331px}
.post .thumb{height:185px}
.post h6{font-size:18.5px;font-weight:500;color:#222;line-height:26px;margin-top:24px}
.post time{display:block;font-size:13px;color:var(--red);margin-top:8px}

/* footer */
.footer{top:1972px;left:0;width:1200px;height:366px;background:var(--footer);color:var(--footer-text)}
.footer h4{position:absolute;font-size:18px;font-weight:500;color:var(--white)}
.footer .red{color:#e0372f;font-size:15px}
.footer .list{position:absolute;font-size:14px;line-height:26px}
.footer .ico{display:flex;align-items:center;gap:12px}
.footer .ico svg{width:13px;height:13px;fill:var(--footer-text)}
.badge{left:782px;top:2044px;width:186px;height:114px;background:var(--white)}
.socials{left:782px;top:2225px;display:flex;gap:10px}
.socials span{width:28px;height:28px;border-radius:50%;background:#6b6b6b}
.bottombar{top:2338px;left:0;width:1200px;height:62px;background:var(--footer-bottom);font-size:12px;color:#9a7a4a;text-align:center;line-height:62px}
</style>
</head>
<body>

<header class="abs topbar">
  <div class="abs contact-line">
    <svg viewBox="0 0 24 24"><path d="M6.6 10.8a15.1 15.1 0 0 0 6.6 6.6l2.2-2.2c.3-.3.7-.4 1-.2 1.1.4 2.3.6 3.6.6.6 0 1 .4 1 1V20c0 .6-.4 1-1 1A17 17 0 0 1 3 4c0-.6.4-1 1-1h3.5c.6 0 1 .4 1 1 0 1.3.2 2.5.6 3.6.1.3 0 .7-.2 1z"/></svg>
    <span>1-855-555-0142</span><span class="sep">|</span>
    <svg viewBox="0 0 24 24"><path d="M2 5h20v14H2z M2 5l10 8 10-8" stroke="#fff" stroke-width="1.5"/></svg>
    <span>contact@lepontdoriole.ca</span>
  </div>
  <div class="abs login-btn">LOG IN <span>⌄</span></div>
  <div class="abs lang">● EN ⌄</div>
</header>

<div class="abs login-panel">
  <div class="field">Username</div>
  <div class="field">Password</div>
  <div class="submit">LOG IN</div>
  <div class="links"><span>Register</span><span>Forgot Password?</span></div>
</div>

<nav class="abs nav">
  <ul>
    <li>HOME</li>
    <li class="has-sub">PRODUCTS</li>
    <li class="has-sub">SUBMISSION</li>
    <li>WHO ARE WE?</li>
    <li>CONTACT U.S</li>
  </ul>
</nav>

<section class="abs hero">
  <div class="abs hero-photo" role="img" aria-label="Photo of a smiling family lying together on the grass in a park"></div>
  <div class="abs brand"><span class="dot"></span>lepontdoriole.ca</div>
  <div class="abs hero-panel">
    <p style="top:34px">Rapide,</p>
    <p style="top:78px">Gratuit et</p>
    <p style="top:122px">Confidentiel</p>
    <p style="top:170px">1-855-555-0142</p>
    <p style="top:238px">Nous desservons</p>
    <p style="top:282px">tout le Québec</p>
  </div>
</section>

<section class="abs categories">
  <div class="cat" style="left:196px">
    <div class="circle" style="background:var(--life)"><svg viewBox="0 0 24 24"><path d="M12 21s-8-5-8-11a4.5 4.5 0 0 1 8-2.8A4.5 4.5 0 0 1 20 10c0 6-8 11-8 11z"/></svg></div>
    <h3>LIFE</h3>
  </div>
  <div class="cat" style="left:470px">
    <div class="circle" style="background:var(--salary)"><svg viewBox="0 0 24 24"><text x="12" y="19" text-anchor="middle" font-size="18" font-weight="700" font-family="Arial">$</text></svg></div>
    <h3>SALARY</h3>
  </div>
  <div class="cat" style="left:735px">
    <div class="circle" style="background:var(--mortgage)"><svg viewBox="0 0 24 24"><path d="M6 3h9l4 4v14H6z M9 10h7v1.5H9z M9 13.5h7V15H9z M9 17h5v1.5H9z" fill-rule="evenodd"/></svg></div>
    <h3>MORTGAGE</h3>
  </div>
  <div class="cat" style="left:1005px">
    <div class="circle" style="background:var(--disease)"><svg viewBox="0 0 24 24"><path d="M10 4h4v6h6v4h-6v6h-4v-6H4v-4h6z"/></svg></div>
    <h3>SERIOUS DISEASES</h3>
  </div>
</section>

<main>
  <div class="abs intro">
    <h1>Find The Best Insurance At The Best Price!</h1>
    <p>Whether you are looking for life insurance, mortgage insurance or else you certainly want to pay the most advantageous price. Navigating among the many offers in the field of insurance can be a real headache. But thanks to the intervention of Financial Security Advisors of Le Pont d'Oriole, we will save you hours of fruitless search, and in addition, you will find an insurance policy that suits you, at a price that fully meets the constraints on your financial situation, whatever it is. We use an innovative, simple and effective, which allows you to shop an insurance policy in the comfort of your home thanks in particular to our insurance quote forms online. Le Pont d'Oriole allows you to find the best price for:</p>
  </div>

  <div class="abs checks">
    <span><svg viewBox="0 0 14 14"><circle cx="7" cy="7" r="7" fill="#d81d1d"/><path d="M3.8 7.2l2.2 2.2 4.2-4.4" stroke="#fff" stroke-width="1.8" fill="none"/></svg>Permanent life insurance - term life insurance</span>
    <span><svg viewBox="0 0 14 14"><circle cx="7" cy="7" r="7" fill="#d81d1d"/><path d="M3.8 7.2l2.2 2.2 4.2-4.4" stroke="#fff" stroke-width="1.8" fill="none"/></svg>Mortgage Insurance - loans</span>
    <span><svg viewBox="0 0 14 14"><circle cx="7" cy="7" r="7" fill="#d81d1d"/><path d="M3.8 7.2l2.2 2.2 4.2-4.4" stroke="#fff" stroke-width="1.8" fill="none"/></svg>Disability Insurance - Disability Insurance</span>
    <span><svg viewBox="0 0 14 14"><circle cx="7" cy="7" r="7" fill="#d81d1d"/><path d="M3.8 7.2l2.2 2.2 4.2-4.4" stroke="#fff" stroke-width="1.8" fill="none"/></svg>Critical illness insurance</span>
  </div>
  <div class="abs rule"></div>

  <article class="feature" style="left:75px;top:1150px">
    <div class="icon"><svg viewBox="0 0 24 24"><path d="M2 11l20-8-8 20-3-9z"/></svg></div>
    <div><h4>How to proceed?</h4><p>Simply fill in the insurance quote online form above, clicking on the insurance category that fits your needs.</p><span class="more">More</span></div>
  </article>
  <article class="feature" style="left:433px;top:1150px">
    <div class="icon"><svg viewBox="0 0 24 24"><circle cx="12" cy="6" r="3"/><circle cx="5.5" cy="10" r="2.5"/><circle cx="18.5" cy="10" r="2.5"/><path d="M6 20c0-5 2.5-8 6-8s6 3 6 8zM1 19c0-3 1.8-5 4.5-5 1 0 1.5.3 1.5.3-1 1.5-1.5 3-1.5 4.7zM23 19c0-3-1.8-5-4.5-5-1 0-1.5.3-1.5.3 1 1.5 1.5 3 1.5 4.7z"/></svg></div>
    <div><h4>Competent financial advisors Security</h4><p>Team Le Pont d'Oriole offers an innovative service in the field of insurance.</p><span class="more">More</span></div>
  </article>
  <article class="feature" style="left:75px;top:1360px">
    <div class="icon"><svg viewBox="0 0 24 24"><path d="M2 6h20v12H2z M12 9a3 3 0 1 0 0 6 3 3 0 0 0 0-6z" fill-rule="evenodd"/></svg></div>
    <div><h4>The importance of not overpaying</h4><p>Disbursing monthly or annually money for insurance is a considerable expense..</p><span class="more">More</span></div>
  </article>
  <article class="feature" style="left:433px;top:1360px">
    <div class="icon"><svg viewBox="0 0 24 24"><path d="M12 3C6 3 2 7 2 12h20c0-5-4-9-10-9z M11 12h2v7a3 3 0 0 1-6 0h2a1 1 0 0 0 2 0z"/></svg></div>
    <div><h4>Insurance: ? How to find</h4><p>The life insurance market premium may seem complex at first.Indeed, insurers offer a variety of products..</p><span class="more">More</span></div>
  </article>
</main>

<aside class="abs quote">
  <h5 style="top:123px;border:none">Product</h5>
  <div class="row" style="top:166px;border-top:1px solid #25397a;padding-top:0"><span>Types of insurance *</span><span class="select">Select <span>⇕</span></span></div>
  <h5 style="top:226px">Applicant</h5>
  <div class="row" style="top:280px"><span>Full Name *</span><span class="input"></span></div>
  <div class="row" style="top:323px"><span>Cities *</span><span class="input"></span></div>
  <div class="row" style="top:366px"><span>Email *</span><span class="input"></span></div>
  <div class="row" style="top:409px"><span>Phone *</span><span class="input"></span></div>
  <div class="row" style="top:452px"><span>Age *</span><span class="input"></span></div>
  <div class="row" style="top:506px;justify-content:flex-start"><span style="width:94px">Gender *</span><span><i class="radio"></i>Men</span><span style="margin-left:22px"><i class="radio"></i>Wife</span></div>
  <h5 style="top:548px">Co-Applicant</h5>
  <div class="row" style="top:596px;justify-content:flex-start"><i class="radio"></i>Add a co-applicant</div>
  <div class="row" style="top:628px;justify-content:flex-start;align-items:flex-start;line-height:20px"><i class="radio" style="margin-top:4px"></i><span style="width:260px">I have read and accept the use and privacy policy of **</span></div>
  <div class="abs captcha" style="top:682px">REGFD</div>
  <div class="abs captcha-input" style="top:682px"></div>
  <div class="abs get-quote" style="top:737px">GET A QUOTE</div>
</aside>
<div class="abs quote-tag">Quote Request</div>

<section class="abs blog">
  <h2>Blog Posts</h2>
  <div class="arrows">‹›</div>
  <article class="post" style="left:75px">
    <div class="thumb" role="img" aria-label="Illustration of an umbrella held over a sketched family and house" style="background:linear-gradient(135deg,#9a9a9a,#d4d4d4)"></div>
    <h6>Duis aliquam nibh a dui iaculis viverra id a velit.</h6><time>Apr 06, 2016</time>
  </article>
  <article class="post" style="left:435px">
    <div class="thumb" role="img" aria-label="Photo of a senior couple signing papers with an advisor" style="background:linear-gradient(135deg,#c9a486,#e8d7c6 60%,#8da0c4)"></div>
    <h6>Duis aliquam nibh a dui iaculis viverra id a velit.</h6><time>Apr 06, 2016</time>
  </article>
  <article class="post" style="left:795px">
    <div class="thumb" role="img" aria-label="Photo of a family in front of their new house under a blue sky" style="background:linear-gradient(#7fb6e6,#c9def0 55%,#7fb54a)"></div>
    <h6>Duis aliquam nibh a dui iaculis viverra id a velit.</h6><time>Apr 06, 2016</time>
  </article>
</section>

<footer class="abs footer">
  <h4 style="left:75px;top:38px">Our Office</h4>
  <div class="list" style="left:75px;top:68px">
    <div class="red">The Head Office</div>
    <div>48 Rue Delorme, La Prairie,</div>
    <div>QC, J5R 1K4</div>
    <div class="ico" style="margin-top:6px"><svg viewBox="0 0 24 24"><path d="M6.6 10.8a15.1 15.1 0 0 0 6.6 6.6l2.2-2.2c.3-.3.7-.4 1-.2 1.1.4 2.3.6 3.6.6.6 0 1 .4 1 1V20c0 .6-.4 1-1 1A17 17 0 0 1 3 4c0-.6.4-1 1-1h3.5c.6 0 1 .4 1 1 0 1.3.2 2.5.6 3.6.1.3 0 .7-.2 1z"/></svg>1-855-555-0142</div>
    <div class="ico"><svg viewBox="0 0 24 24"><path d="M2 5h20v14H2z"/></svg>contact@lepontdoriole.ca</div>
  </div>
  <h4 style="left:75px;top:240px">Hours of Operation</h4>
  <div class="list" style="left:75px;top:270px">
    <div class="red">Our Hours of Operation</div>
    <div>Monday to Friday: 7am to 21hrs</div>
    <div>Sunday: 10hrs to 15hrs</div>
  </div>

  <h4 style="left:395px;top:38px">Towns</h4>
  <div class="list" style="left:395px;top:68px">
    <div>Montreal</div><div>Quebec</div><div>Sherbrooke</div><div>Granby</div><div>Beauce</div><div>three Rivères</div><div>Piedmont</div><div>Saguenay</div><div>Goods</div><div>Chicoutimi</div>
  </div>
  <div class="list" style="left:565px;top:64px">
    <div>Sept-iles</div><div>Rouyn-Noranda</div><div>Val D'Or</div><div>Gatineau</div><div>Victoriaville</div><div>Amqui</div><div>Wolf River</div><div>Chateauguay</div><div>La Prairie</div>
  </div>

  <h4 style="left:782px;top:38px">Member Of</h4>
  <h4 style="left:782px;top:220px">Follow Us</h4>
</footer>
<div class="abs badge" role="img" aria-label="Member organization badge"></div>
<div class="abs socials"><span></span><span></span><span></span><span></span><span></span><span></span></div>
<div class="abs bottombar">Copyright © 2016 Le Pont d'Oriole. For Studio Nordel</div>

</body>
</html>
```